Exclusive beauty salon needs a price list or services booklet

I need a new very attractive flyer for my beauty salon, containing information on the different services and their prices.
In attachment you can find a pdf of the "old" one, but I'd love to have a beautifully designed new one!
I'd love to have a booklet in format 148 x 148 mm, or in US format, containing 12 or 16 pages, but if you can offer other nice looking designs they are welcome!
The services that need to come in the booklet with their prices can all be found on my website: www.atelierverano.be, starting with
Gelaatsverzorging
Wimperverlenging
Suikerontharing
Wimperlifting
Permanente Make Up
Airbrush Tanning

Target Market(s)

woman from 20 to 89 years old

Industry/Entity Type

Beauty Salon

Font styles to use
Sans Serif

Colors

Designer to choose colors to be used in the design.

Requirements
Must have
• a classy nice look, it must contain details about the services from my beauty salon and their prices, and nice pictures.
• The Names, prices and explanations of the services can easily be found on my website: www.atelierverano.be
Nice to have
• In attachment you can find the "old" price list in pdf, what I need now is a "new booklet" with the new logo and updated services price list.
• I need a very nice and attractive looking booklet, classy chique, Paris chique, looking very expensive.
Should not have
• Not too much colors, not too curly, but still feminine

```html
<!DOCTYPE html>
<html lang="nl">
<head>
<meta charset="utf-8">
<title>Permanente Make Up – brochure spread</title>
<link rel="stylesheet" href="https://fonts.googleapis.com/css2?family=Lora:wght@400;500&family=Questrial&display=swap">
<style>
  :root {
    --backdrop: #d9d9d9;
    --paper: #ffffff;
    --paper-shade: #f3f3f3;
    --ink: #2b2b2b;
    --ink-soft: #4a4a4a;
    --teal: #6cc0b6;
    --teal-light: #9fd6cf;
    --rule: #d4d4d4;
    --photo-lips-a: #f2c2c8;
    --photo-lips-b: #e89aa6;
    --photo-group-a: #f6ede6;
    --photo-group-b: #d9b49a;
    --photo-group-c: #7a5a4a;
  }
  * { box-sizing: border-box; margin: 0; padding: 0; }
  html, body { width: 1200px; height: 900px; overflow: hidden; }
  body {
    background: var(--backdrop);
    font-family: "Questrial", sans-serif;
    color: var(--ink);
    position: relative;
  }
  .spread {
    position: absolute;
    left: 50px; top: 175px;
    width: 1100px; height: 550px;
    display: flex;
    box-shadow: 0 10px 28px rgba(0,0,0,.18);
  }
  .page {
    position: relative;
    width: 550px; height: 550px;
    background: var(--paper);
    overflow: hidden;
  }
  .page--left { background: linear-gradient(to right, var(--paper) 88%, var(--paper-shade)); }
  .page--right { background: linear-gradient(to left, var(--paper) 88%, var(--paper-shade)); }

  /* left page */
  .page-title {
    position: absolute; top: 38px; left: 0; width: 550px;
    text-align: center;
    font-family: "Lora", serif; font-weight: 400;
    font-size: 27px; letter-spacing: .3px;
  }
  .title-rule {
    position: absolute; top: 86px; left: 245px;
    width: 60px; height: 2px; background: var(--teal);
  }
  .photo-lips {
    position: absolute; left: 50px; top: 136px;
    width: 205px; height: 168px;
    background: radial-gradient(ellipse at 55% 30%, var(--photo-lips-b), var(--photo-lips-a) 70%);
  }
  .advice-title {
    position: absolute; left: 50px; top: 318px; width: 205px;
    text-align: center; color: var(--teal);
    font-size: 14px; letter-spacing: 1.2px; font-weight: 400;
  }
  .advice-text {
    position: absolute; left: 62px; top: 342px; width: 185px;
    font-size: 9px; line-height: 14px; text-align: justify; color: var(--ink-soft);
    hyphens: auto;
  }
  .intro-text {
    position: absolute; left: 280px; top: 132px; width: 224px;
    font-size: 11px; line-height: 21px; text-align: justify; color: var(--ink-soft);
    hyphens: auto;
  }
  .footer-rule {
    position: absolute; left: 50px; top: 502px; width: 452px; height: 1px; background: var(--rule);
  }
  .page-number {
    position: absolute; left: 50px; top: 512px; width: 25px; height: 25px;
    background: var(--teal); color: #fff; font-size: 14px;
    display: flex; align-items: center; justify-content: center;
  }
  .footer-label {
    position: absolute; left: 85px; top: 515px;
    color: var(--teal-light); font-size: 14px;
  }

  /* right page */
  .section-title {
    font-family: "Lora", serif; font-weight: 500; color: var(--teal);
  }
  .what-title { position: absolute; left: 48px; top: 26px; font-size: 17px; }
  .what-text {
    position: absolute; left: 48px; top: 62px; width: 200px;
    font-size: 7px; line-height: 10.5px; color: var(--ink-soft);
    hyphens: auto;
  }
  .when-title {
    position: absolute; left: 282px; top: 62px; width: 200px;
    font-size: 17px; line-height: 19px;
  }
  .when-list {
    position: absolute; left: 282px; top: 118px; width: 200px;
    list-style: none; font-size: 7.4px; line-height: 12px; color: var(--ink-soft);
  }
  .when-list li { padding-left: 7px; position: relative; margin-bottom: 2px; }
  .when-list li::before {
    content: ""; position: absolute; left: 0; top: 5px;
    width: 3px; height: 3px; border-radius: 50%; background: var(--ink-soft);
  }
  .photo-group {
    position: absolute; left: 0; top: 320px; width: 550px; height: 230px;
    background:
      linear-gradient(to bottom, var(--paper) 0%, rgba(255,255,255,0) 25%),
      linear-gradient(to right, var(--photo-group-a) 0%, var(--photo-group-b) 40%, var(--photo-group-c) 55%, var(--photo-group-b) 75%, var(--photo-group-a) 100%);
  }
</style>
</head>
<body>
  <div class="spread">
    <section class="page page--left">
      <h1 class="page-title">Permanente Make Up</h1>
      <div class="title-rule"></div>

      <div class="photo-lips" role="img" aria-label="Close-up photo of pink lips with a lip pencil"></div>

      <h2 class="advice-title">GRATIS ADVIESGESPREK</h2>
      <p class="advice-text">Het is mogelijk om eerst op consult te komen om te bespreken wat je graag zou willen. De gewenste vorm van uw wenkbrauwen, lippen of eyeliner wordt samen uitgetekend, we zoeken dan samen de kleur uit die jou gezicht het beste ophaalt en het mooiste bij je past, zodat je een idee krijgt van het resultaat.</p>

      <div class="intro-text">
        <p>Permanente make-up zit altijd goed en zorgt ervoor dat je er altijd verzorgd uitziet. Eyeliners, lipliners of wenkbrauw-accenten worden permanent aangebracht. Zo zie je er tijdens het sporten, als je uit bed stapt, als je op vakantie uit zee komt, als je een flinke strandwandeling maakt of in de regen hebt gefietst, toch verzorgd uit.</p>
        <p>Permanente make-up blijft altijd op z’n plaats, doordoor oogt je gezicht ook na het verwijderen van je make-up niet ‘kaal’. De aangebrachte accenten zorgen voor een sprekend gezicht en dat scheelt dagelijks een hoop tijd!</p>
      </div>

      <div class="footer-rule"></div>
      <div class="page-number">5</div>
      <div class="footer-label">Permanente Make Up</div>
    </section>

    <section class="page page--right">
      <h2 class="section-title what-title">Wat is permanente make up?</h2>
      <div class="what-text">
        <p>Permanente make-up, micro-pigmentatie, cosmetische tatoeage, esthetische tatoeage of dermografie is een verfijnde tatoeage/ pigmentatietechniek van inplanting van hoge kwaliteitspigmenten op basis van mineralen onder de epidermis (=opperhuid).</p>
        <p>De behandeling wordt in uiterst hygiënische en veilige omstandigheden uitgevoerd met een professioneel apparaat en éénmalige, steriele naalden. Het doel van permanente make-up is het esthetische aspect verbeteren, waarbij het welzijn van de klant centraal staat.</p>
        <p>Het beoogde resultaat is natuurlijk en dit op langere termijn. Indien je op zoek bent naar een esthetische verbetering, een fysische correctie, een oplossing voor een specifiek fysisch probleem op je gelaat of lichaam kan permanente make up de juiste oplossing zijn.</p>
      </div>

      <h2 class="section-title when-title">Wanneer is permanente make- up zinvol?</h2>
      <ul class="when-list">
        <li>U wil er beter uitzien waardoor u zich beter voelt</li>
        <li>U wil een natuurlijke uitstraling, elke dag opnieuw</li>
        <li>U zoekt een waterbestendige make-up, geen make-up die uitloopt wanneer u geniet van wellness</li>
        <li>Omwille van motorische of gezichtsproblemen is het moeilijk u correcte make-up aan te brengen</li>
        <li>U beheerst niet de tekenkunst om u juist te maquilleren</li>
        <li>Beroepshalve bent u genoodzaakt er steeds gemaquilleerd, verzorgd uit te zien</li>
      </ul>

      <div class="photo-group" role="img" aria-label="Photo of three smiling women with natural make-up"></div>
    </section>
  </div>
</body>
</html>
```